Roadside building business signage for a holistic health clinic.

Replace signs as shown in the attached file. They are perforated stickers that go on the windows as shown. Looking for something that has our logo and says the name of the practice with logo (Fernridge Health & Wellness) also boldly says Acupuncture, IV Vitamins, and Holistic Health.
Possibly our phone number as well 318-562-7041
Updates

Please don't use pink except the logo. Earthy, organic tone colors appreciated.

Need of eye catching window signage of a holistic clinic on a brick building. Pink, purple, sage green, white color. Logo is pink on a white background. Please don't overload with too much pink. Words to include are "Fernridge Health and Wellness(name of business)", "Direct Primary Care", " Medical acupuncture", "IV Vitamin Therapy", "fernridgecareclinic.example","318-562-7041".

Target Market(s)

People will see in their cars passing by the building. Busy roadside so need to be visible while passing in fast speed.

Industry/Entity Type

Health & Wellness

Font styles to use
Sans Serif

Colors

Designer to choose colors to be used in the design.

Requirements
Must have
• On sign must have words Holistic Medicine, Medical Acupuncture, Direct Primary Care and IV vitamins.
Nice to have
• Simple, minimalistic, artistic yet has clear message. White, Black, Violet, Pink (logo), Dark green, Sage green.
Should not have
• Bold colors (red, yellow, blue), same tone colors. Blue waves on the current signage (uploaded file) must go.

```html
<!DOCTYPE html>
<html lang="en">
<head>
<meta charset="utf-8">
<title>Fernridge Health &amp; Wellness – Window Signs</title>
<link rel="stylesheet" href="https://fonts.googleapis.com/css2?family=Poppins:wght@500;600;700&display=swap">
<style>
  :root{
    --backdrop:#b3b3b3;
    --paper:#ffffff;
    --forest:#0c4c3b;
    --forest-ink:#0e4a3a;
    --logo-pink:#d8337f;
    --sage:#9cbf9f;
    --sage-deep:#6f9f7a;
    --violet:#6b4c8a;
    --blush:#f7f4f0;
    --charcoal:#333333;
  }
  *{margin:0;padding:0;box-sizing:border-box}
  html,body{width:1200px;height:3294px;overflow:hidden}
  body{background:var(--backdrop);font-family:"Poppins",sans-serif;position:relative}

  .sign{position:absolute;left:151px;width:898px;height:898px;overflow:hidden;
        box-shadow:0 4px 14px rgba(0,0,0,.28)}
  .sign--brand{top:700px;background:var(--paper)}
  .sign--services{top:1696px;background:var(--forest)}

  /* brand panel */
  .brand-mark{position:absolute;left:349px;top:200px;width:200px;height:200px;border-radius:50%;
              background:var(--logo-pink)}
  .brand-name{position:absolute;left:0;top:420px;width:100%;text-align:center;
              color:var(--forest-ink);font-weight:600;line-height:1}
  .brand-name__main{display:block;font-size:104px;letter-spacing:6px}
  .brand-name__sub{display:block;font-size:34px;letter-spacing:12px;margin-top:26px}
  .floral-band{position:absolute;left:0;bottom:0;width:100%;height:216px;
               background:linear-gradient(180deg,var(--paper) 0%,var(--blush) 45%,#e3eee3 100%)}

  /* services panel */
  .leaf-texture{position:absolute;background:linear-gradient(160deg,rgba(156,191,159,.14),rgba(156,191,159,0))}
  .leaf-texture--left{left:0;top:120px;width:150px;height:360px}
  .leaf-texture--right{right:0;top:440px;width:200px;height:440px}
  .header-arc{position:absolute;left:0;top:0}
  .services-mark{position:absolute;left:426px;top:36px;width:80px;height:80px;border-radius:50%;
                 background:var(--logo-pink)}
  .services-name{position:absolute;left:32px;top:140px;width:870px;text-align:center;
                 color:var(--forest-ink);font-weight:600;line-height:1}
  .services-name__main{display:block;font-size:64px;letter-spacing:4px}
  .services-name__sub{display:block;font-size:22px;letter-spacing:8px;margin-top:16px}
  .services-web{position:absolute;left:32px;top:290px;width:870px;text-align:center;
                color:var(--violet);font-weight:500;font-size:24px;letter-spacing:.5px}

  .service-list{position:absolute;left:96px;top:438px;list-style:none}
  .service{display:flex;align-items:center;height:84px}
  .service__icon{width:72px;height:72px;border-radius:50%;background:var(--paper);
                 border:4px solid var(--sage);display:flex;align-items:center;justify-content:center;
                 flex:none}
  .service__label{margin-left:38px;color:var(--paper);font-weight:600;font-size:44px;
                  letter-spacing:-.5px;line-height:1;white-space:nowrap}

  .phone-pill{position:absolute;left:157px;top:804px;width:591px;height:110px;
              background:var(--paper);border-radius:55px 55px 0 0;
              display:flex;align-items:center;justify-content:center;gap:22px;padding-bottom:16px}
  .phone-pill__number{font-weight:700;font-size:56px;color:var(--charcoal);letter-spacing:1px}
</style>
</head>
<body>

<section class="sign sign--brand" aria-label="Brand window sign">
  <div class="brand-mark"></div>
  <h1 class="brand-name">
    <span class="brand-name__main">FERNRIDGE</span>
    <span class="brand-name__sub">HEALTH &amp; WELLNESS</span>
  </h1>
  <div class="floral-band" role="img" aria-label="Light line-drawn botanical flowers and leaves along the bottom edge"></div>
</section>

<section class="sign sign--services" aria-label="Services window sign">
  <div class="leaf-texture leaf-texture--left" role="img" aria-label="Faint line-drawn leaves"></div>
  <div class="leaf-texture leaf-texture--right" role="img" aria-label="Faint line-drawn botanical flowers"></div>

  <svg class="header-arc" width="898" height="898" viewBox="0 0 898 898" aria-hidden="true">
    <circle cx="466" cy="-50" r="452" fill="var(--sage)"/>
    <circle cx="466" cy="-50" r="445" fill="var(--paper)"/>
  </svg>

  <div class="services-mark"></div>
  <h2 class="services-name">
    <span class="services-name__main">FERNRIDGE</span>
    <span class="services-name__sub">HEALTH &amp; WELLNESS</span>
  </h2>
  <p class="services-web">fernridgecareclinic.example</p>

  <ul class="service-list">
    <li class="service">
      <span class="service__icon">
        <svg width="40" height="40" viewBox="0 0 50 50" aria-hidden="true">
          <rect x="5" y="22" width="40" height="8" rx="2" fill="var(--charcoal)"/>
          <rect x="10" y="30" width="30" height="14" fill="none" stroke="var(--charcoal)" stroke-width="3"/>
          <line x1="16" y1="37" x2="34" y2="37" stroke="var(--violet)" stroke-width="3"/>
          <line x1="25" y1="6" x2="25" y2="18" stroke="var(--violet)" stroke-width="3"/>
          <line x1="19" y1="12" x2="31" y2="12" stroke="var(--violet)" stroke-width="3"/>
        </svg>
      </span>
      <span class="service__label">DIRECT PRIMARY CARE</span>
    </li>
    <li class="service">
      <span class="service__icon">
        <svg width="40" height="40" viewBox="0 0 50 50" aria-hidden="true">
          <rect x="5" y="30" width="40" height="10" rx="3" fill="var(--charcoal)"/>
          <circle cx="14" cy="24" r="6" fill="var(--violet)"/>
          <line x1="26" y1="8" x2="26" y2="28" stroke="var(--charcoal)" stroke-width="2"/>
          <line x1="34" y1="10" x2="34" y2="28" stroke="var(--charcoal)" stroke-width="2"/>
        </svg>
      </span>
      <span class="service__label">MEDICAL ACUPUNCTURE</span>
    </li>
    <li class="service">
      <span class="service__icon">
        <svg width="40" height="40" viewBox="0 0 50 50" aria-hidden="true">
          <path d="M25 6 C18 12 18 20 25 24 C32 20 32 12 25 6Z" fill="var(--sage-deep)"/>
          <rect x="9" y="28" width="32" height="14" rx="7" fill="var(--charcoal)"/>
          <rect x="25" y="28" width="16" height="14" rx="7" fill="var(--violet)"/>
        </svg>
      </span>
      <span class="service__label">HOLISTIC MEDICINE</span>
    </li>
    <li class="service">
      <span class="service__icon">
        <svg width="40" height="40" viewBox="0 0 50 50" aria-hidden="true">
          <rect x="14" y="6" width="22" height="28" rx="4" fill="none" stroke="var(--charcoal)" stroke-width="3"/>
          <line x1="19" y1="15" x2="31" y2="15" stroke="var(--violet)" stroke-width="2.5"/>
          <line x1="19" y1="21" x2="31" y2="21" stroke="var(--violet)" stroke-width="2.5"/>
          <line x1="25" y1="34" x2="25" y2="46" stroke="var(--charcoal)" stroke-width="3"/>
        </svg>
      </span>
      <span class="service__label">IV VITAMINS</span>
    </li>
  </ul>

  <div class="phone-pill">
    <svg width="52" height="52" viewBox="0 0 24 24" aria-hidden="true">
      <path fill="var(--forest)" d="M6.6 10.8a15.1 15.1 0 0 0 6.6 6.6l2.2-2.2a1 1 0 0 1 1-.25 11.4 11.4 0 0 0 3.6.57 1 1 0 0 1 1 1V20a1 1 0 0 1-1 1A17 17 0 0 1 3 4a1 1 0 0 1 1-1h3.5a1 1 0 0 1 1 1c0 1.25.2 2.45.57 3.57a1 1 0 0 1-.25 1z"/>
    </svg>
    <span class="phone-pill__number">318-562-7041</span>
  </div>
</section>

</body>
</html>
```